Web Design Project for SEARCH ENGINE !

We need a website design for torrents search engine.

The Website will be www.Qentrova.com

Qentrova is a a search engine for torrents.
Qentrova search and index torrents results from all torrents sites.

We will need:
Logo
WebSite Design
slogen (optional)

we need only PSDs - no codded pages are needed !

Design to the following screen Size & resolution: 1024 x 768

***PLEASE DOWNLOAD ATTACHED FILE !

```html
<!DOCTYPE html>
<html lang="en">
<head>
<meta charset="utf-8">
<title>Qentrova – Find what you need</title>
<link rel="stylesheet" href="https://fonts.googleapis.com/css2?family=Source+Sans+3:ital,wght@0,400;0,600;0,700;1,400&display=swap">
<style>
  :root {
    --link: #1f5fb0;
    --rule: #8fa6c4;
    --ink: #111111;
    --brand: #6d97c0;
    --brand-dark: #4f7ea9;
    --field-border: #4a90d4;
    --button-top: #4aa0e0;
    --button-bottom: #1f74c0;
    --placeholder: #9a9a9a;
    --page: #ffffff;
  }
  * { box-sizing: border-box; margin: 0; padding: 0; }
  html, body { width: 1200px; height: 800px; overflow: hidden; background: var(--page); }
  body { position: relative; font-family: "Source Sans 3", Arial, sans-serif; color: var(--ink); }

  .top-bar {
    position: absolute; left: 0; top: 0; width: 1200px; height: 58px;
    border-bottom: 1px solid var(--rule);
  }
  .main-nav { position: absolute; left: 49px; top: 27px; display: flex; gap: 17px; }
  .main-nav a, .account a, .language a {
    color: var(--link); font-size: 17px; text-decoration: underline;
  }
  .nav-more { display: inline-flex; align-items: center; gap: 5px; }
  .language { position: absolute; left: 885px; top: 27px; display: flex; align-items: center; gap: 11px; }
  .flag { width: 25px; height: 15px; background: linear-gradient(135deg, #2b3f8f 0 35%, #d8d8e8 35% 42%, #c8242c 42% 58%, #d8d8e8 58% 65%, #2b3f8f 65%); }
  .account { position: absolute; left: 1025px; top: 27px; display: flex; gap: 14px; color: var(--link); font-size: 17px; }

  .brand {
    position: absolute; left: 0; top: 175px; width: 1250px;
    display: flex; justify-content: center; align-items: center; gap: 14px;
  }
  .brand-mark { width: 46px; height: 46px; background: var(--brand-dark); border-radius: 6px; }
  .brand-name { font-size: 66px; font-weight: 700; color: var(--brand); line-height: 1; }
  .slogan {
    position: absolute; left: 0; top: 294px; width: 1250px; text-align: center;
    font-size: 21px; font-weight: 700; color: var(--ink);
  }

  .search {
    position: absolute; left: 270px; top: 357px; width: 711px; height: 54px;
    border: 2px solid var(--field-border); border-radius: 27px;
    box-shadow: 0 3px 5px rgba(0,0,0,0.25); overflow: hidden; display: flex; background: var(--page);
  }
  .search-field {
    flex: 1; border: 0; outline: 0; padding-left: 28px;
    font-family: inherit; font-style: italic; font-size: 27px; color: var(--placeholder); background: transparent;
  }
  .search-field::placeholder { color: var(--placeholder); }
  .search-button {
    width: 68px; border: 0; background: linear-gradient(var(--button-top), var(--button-bottom));
    display: flex; align-items: center; justify-content: center;
  }

  .social { position: absolute; left: 520px; top: 658px; display: flex; gap: 39px; }
  .social span { width: 19px; height: 19px; border-radius: 3px; display: block; }
  .social .s1 { background: #3b5a9a; }
  .social .s2 { background: #333333; }
  .social .s3 { background: #2a6fa8; }
  .social .s4 { background: #4cc0ec; }

  .footer-nav {
    position: absolute; left: 0; top: 694px; width: 1232px;
    display: flex; justify-content: center; gap: 18px; font-size: 16px; color: var(--link);
  }
  .footer-nav a { color: var(--link); text-decoration: none; }
  .copyright {
    position: absolute; left: 0; top: 732px; width: 1232px; text-align: center;
    font-size: 15.5px; line-height: 24px; color: var(--ink);
  }
</style>
</head>
<body>
  <header class="top-bar">
    <nav class="main-nav">
      <a href="#">Qentrova</a>
      <a href="#">Film</a>
      <a href="#">Music</a>
      <a href="#">Game</a>
      <a href="#">Clip</a>
      <a href="#">Video</a>
      <a href="#">Top 100</a>
      <a href="#" class="nav-more">More
        <svg width="13" height="9" viewBox="0 0 13 9" aria-hidden="true"><path d="M0 0h13L6.5 9z" fill="#1f5fb0"/></svg>
      </a>
    </nav>
    <div class="language">
      <span class="flag" role="img" aria-label="British flag"></span>
      <a href="#">English</a>
    </div>
    <div class="account">
      <a href="#">Log in</a><span>|</span><a href="#">Sign up</a>
    </div>
  </header>

  <div class="brand">
    <span class="brand-mark"></span>
    <span class="brand-name">Qentrova</span>
  </div>
  <p class="slogan">Find what you need</p>

  <form class="search">
    <input class="search-field" type="text" placeholder="search...">
    <button class="search-button" type="button" aria-label="Search">
      <svg width="28" height="28" viewBox="0 0 28 28" aria-hidden="true">
        <circle cx="11" cy="11" r="8" fill="none" stroke="#fff" stroke-width="3.5"/>
        <path d="M17 17l8 8" stroke="#fff" stroke-width="5" stroke-linecap="round"/>
      </svg>
    </button>
  </form>

  <div class="social" aria-label="Social links">
    <span class="s1"></span><span class="s2"></span><span class="s3"></span><span class="s4"></span>
  </div>

  <nav class="footer-nav">
    <a href="#">Home</a><span>|</span>
    <a href="#">Privacy Policy</a><span>|</span>
    <a href="#">Terms of Use</a><span>|</span>
    <a href="#">Contact US</a>
  </nav>
  <p class="copyright">Copyright 2011 © Qentrova.com<br>All rights reserved</p>
</body>
</html>
```